Spin Days 4 Fun business card

Spin Days 4 Fun is a national UK campaign that promotes the value of play for children. The website has recently undergone a redesign and will soon be going live, this business card design will need to reflect the new website's design and colour scheme, etc.
Key wording/info for inclusion (front)
- Strapline titles
A bit of Fun each morning (in caps)
giving you great free play ideas, everyday!
- Logo
Key wording for inclusion (rear)
- Download our free play app - Spin Days 4 Fun
- Visit our website - www.spindays4fun.co.uk
- To share hints and tips with other parents
www.facebook.com/spindaysforfun
- Want to get involved in the campaign? No matter who you are we would love to hear from you! Email - getinvolved@spindaysforfun.co.uk
Social media icons
Facebook facebook.com/spindays4fun
Twitter @spindays4fun
Youtube youtube.com/spindaysforfun
The target audience is parents of young children up to the age of 12.
Please note that all attached graphics are the property of the Northern Game & Craft Federation and must only be used for the purpose of this project.
Updates
Please note the design we are seeking will be in a business card 'shape' but will not be for a specific 'person' or name as such. We are looking for a colourful and modern design which is not 'corporate. Thank you.
Target Market(s)
Industry/Entity Type
Business
Look and feel

```html
<!DOCTYPE html>
<html lang="en">
<head>
<meta charset="utf-8">
<title>Spin Days 4 Fun – Business Card</title>
<link href="https://fonts.googleapis.com/css2?family=Exo+2:wght@400;500;600;700&display=swap" rel="stylesheet">
<style>
  :root {
    --page-bg: #e6e7ea;
    --card-bg: #ffffff;
    --purple: #6a4c9c;
    --ink: #3a3a3f;
    --ink-light: #55555c;
    --pink: #ea5a8c;
    --rule-light: #ececf0;
  }
  * { box-sizing: border-box; margin: 0; padding: 0; }
  html, body {
    width: 1052px;
    height: 1200px;
    overflow: hidden;
    background: var(--page-bg);
    font-family: "Exo 2", sans-serif;
  }
  .sheet { position: relative; width: 1052px; height: 1200px; }
  .card {
    position: absolute;
    left: 76px;
    width: 900px;
    height: 514px;
    background: var(--card-bg);
    box-shadow: 0 10px 24px rgba(0,0,0,0.12);
    overflow: hidden;
  }
  .card--back { top: 58px; }
  .card--front { top: 628px; }

  .brand {
    position: absolute;
    display: flex;
    align-items: center;
    gap: 12px;
    white-space: nowrap;
  }
  .brand__dot {
    flex: none;
    width: 30px;
    height: 30px;
    border-radius: 50%;
    background: var(--pink);
  }
  .brand__name {
    font-weight: 700;
    color: var(--purple);
    line-height: 1;
  }
  .card--back .brand { left: 50%; top: 50%; transform: translate(-50%, -50%); }
  .card--back .brand__name { font-size: 52px; }
  .card--front .brand { right: 50px; top: 138px; }
  .card--front .brand__name { font-size: 42px; }

  .strapline { position: absolute; left: 60px; top: 118px; }
  .strapline__title {
    font-size: 22px;
    font-weight: 600;
    letter-spacing: 1px;
    color: var(--purple);
    white-space: nowrap;
  }
  .strapline__sub {
    margin-top: 4px;
    font-size: 16px;
    font-weight: 500;
    color: var(--ink);
    white-space: nowrap;
  }
  .strapline__rule {
    position: absolute;
    left: 0; top: 206px;
    width: 420px; height: 2px;
    background: var(--purple);
  }
  .card__divider {
    position: absolute;
    left: 0; right: 0; top: 216px;
    height: 1px;
    background: var(--rule-light);
  }

  .contact-strip {
    position: absolute;
    left: 70px; top: 268px; bottom: 0;
    width: 64px;
    background: var(--purple);
    padding-top: 12px;
  }
  .contact-strip__icon {
    height: 30px;
    display: flex;
    align-items: center;
    justify-content: center;
  }
  .contact-strip__icon svg { width: 18px; height: 18px; }
  .contact-strip__icon--social { margin-top: 20px; }

  .contact-list {
    position: absolute;
    left: 150px; top: 280px;
    list-style: none;
    font-size: 15px;
    line-height: 30px;
    color: var(--ink-light);
    white-space: nowrap;
  }
  .contact-list strong { font-weight: 600; color: var(--ink); }

  .social-row {
    position: absolute;
    left: 150px; top: 420px;
    display: flex;
    gap: 22px;
    list-style: none;
    font-size: 14px;
    line-height: 30px;
    color: var(--ink-light);
    white-space: nowrap;
  }
  .social-row li { display: flex; align-items: center; gap: 7px; }
  .social-row__mark {
    width: 12px; height: 12px;
    border-radius: 50%;
    background: var(--purple);
  }
</style>
</head>
<body>
<main class="sheet">

  <section class="card card--back" aria-label="Card back">
    <div class="brand">
      <span class="brand__dot"></span>
      <span class="brand__name">Spin Days 4 Fun</span>
    </div>
  </section>

  <section class="card card--front" aria-label="Card front">
    <div class="strapline">
      <p class="strapline__title">A BIT OF FUN EACH MORNING</p>
      <p class="strapline__sub">giving you great free play ideas, everyday!</p>
    </div>
    <div class="strapline__rule"></div>
    <div class="card__divider"></div>

    <div class="brand">
      <span class="brand__dot"></span>
      <span class="brand__name">Spin Days 4 Fun</span>
    </div>

    <div class="contact-strip" aria-hidden="true">
      <div class="contact-strip__icon">
        <svg viewBox="0 0 24 24" fill="none" stroke="#fff" stroke-width="1.8"><rect x="7" y="2.5" width="10" height="19" rx="2"/><path d="M11 18.5h2"/></svg>
      </div>
      <div class="contact-strip__icon">
        <svg viewBox="0 0 24 24" fill="none" stroke="#fff" stroke-width="1.6"><circle cx="12" cy="12" r="9"/><ellipse cx="12" cy="12" rx="4" ry="9"/><path d="M3 12h18"/></svg>
      </div>
      <div class="contact-strip__icon">
        <svg viewBox="0 0 24 24" fill="#fff"><path d="M4 4h16v11H9l-5 4z"/></svg>
      </div>
      <div class="contact-strip__icon">
        <svg viewBox="0 0 24 24"><path d="M3 5h18v14H3z" fill="#fff"/><path d="M3 5l9 7 9-7" fill="none" stroke="#6a4c9c" stroke-width="1.6"/></svg>
      </div>
      <div class="contact-strip__icon contact-strip__icon--social">
        <svg viewBox="0 0 24 24" fill="#fff" stroke="#fff" stroke-width="1.6"><circle cx="18" cy="5" r="3"/><circle cx="6" cy="12" r="3"/><circle cx="18" cy="19" r="3"/><path d="M8.6 10.7l6.8-4M8.6 13.3l6.8 4" fill="none"/></svg>
      </div>
    </div>

    <ul class="contact-list">
      <li><strong>Download our free play app</strong> – Spin Days 4 Fun</li>
      <li><strong>Visit our website</strong> – www.spindays4fun.co.uk</li>
      <li><strong>Share hints &amp; tips with other parents</strong> – www.facebook.com/spindaysforfun</li>
      <li><strong>Want to get involved?</strong> Email – getinvolved@spindaysforfun.co.uk</li>
    </ul>

    <ul class="social-row">
      <li><span class="social-row__mark"></span>facebook.com/spindays4fun</li>
      <li><span class="social-row__mark"></span>@spindays4fun</li>
      <li><span class="social-row__mark"></span>youtube.com/spindaysforfun</li>
    </ul>
  </section>

</main>
</body>
</html>
```